VORTAL MED -DIAGNOSTIC CENTRE FOR IMAGES

Our Activity provides diagnostic services for images (RMI, Tac, RX, Ultrasound etc.)
We would like to create a broschure that illustrates our services.
We would like to give maximum attention to the Diagnostic service dedicated to "HEART", therefore maximum evidence to the world of Cardiology.
In the background we would like to highlight the other diagnostic services dedicated to the Rest of the Body (Brain, Knees Legs etc.)
Target Market(s)
PERSONS WHO NEED TO PERFORM DIAGNOSTIC TESTS (MRI, CT, ULTRASOUND, RX ETC.)
Industry/Entity Type
HEALTH
Requirements
Must have
- The company logo, must have diagnostic images (MRI, CT, X-ray, ultrasound), must be simple and intuitive, which is harmonious with the colors of our company logo
Should not have
- Colours that are not in harmony with our company logo

```html
<!DOCTYPE html>
<html lang="en">
<head>
<meta charset="utf-8">
<title>Vortal Med – Cardiac Imaging Brochure</title>
<link href="https://fonts.googleapis.com/css2?family=Montserrat:wght@400;500;700;800&display=swap" rel="stylesheet">
<style>
  :root {
    --navy: #023a62;
    --navy-deep: #03306a;
    --sky: #0088b8;
    --bright-blue: #0a84f5;
    --cyan-line: #1ec0f0;
    --bubble: #d4e9fb;
    --paper-left: #f5f5f5;
    --paper-right: #f0f9fd;
    --white: #ffffff;
    --lilac: #b39cf5;
    --teal: #13a89e;
    --brand-blue: #1e6fc0;
  }
  * { margin: 0; padding: 0; box-sizing: border-box; }
  html, body { width: 1200px; height: 800px; overflow: hidden; }
  body { font-family: "Montserrat", Arial, sans-serif; background: var(--paper-left); }
  .brochure { position: relative; width: 1200px; height: 800px; overflow: hidden; }

  .panel-left { position: absolute; left: 0; top: 0; width: 600px; height: 800px; background: var(--paper-left); }
  .panel-right { position: absolute; left: 600px; top: 0; width: 600px; height: 800px; background: var(--paper-right); }

  .bubble { position: absolute; border-radius: 50%; background: var(--bubble); }

  .doctor-photo {
    position: absolute; left: 90px; top: 0; width: 420px; height: 352px;
    background: linear-gradient(160deg, #0795c6, var(--sky));
    border-bottom-right-radius: 42px;
    box-shadow: 2px 3px 0 var(--lilac);
  }

  .about-card {
    position: absolute; left: 0; top: 307px; width: 398px; height: 283px;
    background: linear-gradient(180deg, var(--navy), var(--navy-deep));
    border-radius: 0 34px 34px 0;
    color: var(--white); padding: 40px 30px 0 30px;
  }
  .about-card h2 { font-weight: 500; font-size: 27px; letter-spacing: 0.5px; margin-bottom: 10px; }
  .about-card p { font-size: 12.4px; line-height: 19px; margin-bottom: 19px; }

  .call-box {
    position: absolute; left: 0; top: 631px; width: 300px; height: 64px;
    background: var(--white); border: 1px solid var(--cyan-line); border-left: none;
    border-radius: 0 32px 32px 0; display: flex; align-items: center; padding-left: 38px;
    color: var(--navy);
  }
  .call-box svg { margin-right: 11px; }
  .call-label { font-size: 13px; font-weight: 500; margin-right: 9px; }
  .call-number { font-size: 20px; font-weight: 800; }

  .footer-band { position: absolute; left: 0; top: 740px; width: 1200px; height: 60px; background: var(--navy); }
  .social-list { position: absolute; left: 37px; top: 757px; display: flex; align-items: center; gap: 0; list-style: none; }
  .social-list li { width: 25px; height: 25px; background: var(--white); border-radius: 5px; }
  .social-list .divider { width: 1px; height: 22px; background: #6f8aa6; border-radius: 0; margin: 0 14px; }

  .scan-photo { position: absolute; left: 755px; top: 0; width: 445px; height: 480px; }

  .headline-card {
    position: absolute; left: 650px; top: 361px; width: 500px; height: 234px;
    background: linear-gradient(180deg, var(--navy), var(--navy-deep));
    border-radius: 30px; color: var(--white); text-align: center; padding-top: 81px;
  }
  .headline-card h1 { font-weight: 800; font-size: 32px; line-height: 38px; letter-spacing: 0.2px; }
  .headline-card .tagline { font-size: 13px; font-weight: 500; margin-top: 14px; }

  .logo-plate {
    position: absolute; left: 600px; top: 701px; width: 348px; height: 99px;
    background: var(--white); border-top: 2px solid var(--bright-blue);
    border-right: 2px solid var(--bright-blue); border-top-right-radius: 30px;
    display: flex; align-items: center; justify-content: center; gap: 10px;
  }
  .logo-dot { width: 14px; height: 14px; border-radius: 50%; background: var(--teal); }
  .logo-name { font-size: 30px; font-weight: 700; color: var(--brand-blue); letter-spacing: 0.5px; }

  .outline-shape { position: absolute; }
</style>
</head>
<body>
<main class="brochure">
  <section class="panel-left">
    <div class="bubble" style="left:-42px; top:108px; width:132px; height:132px;"></div>
    <div class="doctor-photo" role="img" aria-label="Portrait of a cardiologist in a white coat with a stethoscope"></div>

    <svg class="outline-shape" style="left:320px; top:585px;" width="130" height="115" viewBox="0 0 130 115" aria-hidden="true">
      <path d="M6 5 Q0 20 12 32 L92 108 Q108 118 118 104 Q126 92 116 82 L44 5" fill="none" stroke="var(--cyan-line)" stroke-width="1"/>
    </svg>

    <article class="about-card">
      <h2>ABOUT US</h2>
      <p>At Vortal Med, we are dedicated to revolutionizing diagnostic healthcare through our commitment to accuracy, innovation, and compassionate patient care.</p>
      <p>With a focus on cardiac health, our team of experienced medical professionals combines cutting-edge technology with expertise to provide unparalleled diagnostic services.</p>
    </article>

    <div class="call-box">
      <svg width="25" height="25" viewBox="0 0 24 24" aria-hidden="true">
        <circle cx="12" cy="12" r="12" fill="var(--navy)"/>
        <path d="M8.2 6.5l1.8-.4 1.2 2.8-1.3 1a7 7 0 0 0 3.3 3.3l1-1.3 2.8 1.2-.4 1.8c-.1.5-.6.8-1.1.8A9.3 9.3 0 0 1 7.4 7.6c0-.5.3-1 .8-1.1z" fill="var(--white)"/>
      </svg>
      <span class="call-label">Call Us:</span>
      <span class="call-number">555-014-2298</span>
    </div>
  </section>

  <section class="panel-right">
    <div class="bubble" style="left:-36px; top:-28px; width:136px; height:136px;"></div>
    <div class="bubble" style="left:-34px; top:487px; width:132px; height:132px;"></div>
    <div class="bubble" style="left:500px; top:646px; width:134px; height:134px;"></div>

    <svg class="outline-shape" style="left:507px; top:602px;" width="95" height="50" viewBox="0 0 95 50" aria-hidden="true">
      <path d="M95 1 H24 A24 24 0 0 0 24 49 H95" fill="none" stroke="var(--cyan-line)" stroke-width="1"/>
    </svg>
    <svg class="outline-shape" style="left:414px; top:676px;" width="50" height="66" viewBox="0 0 50 66" aria-hidden="true">
      <path d="M1 66 V24 A24 24 0 0 1 49 24 V66" fill="none" stroke="var(--cyan-line)" stroke-width="1"/>
    </svg>
  </section>

  <svg class="scan-photo" viewBox="0 0 445 480" role="img" aria-label="Photograph of an MRI scanner with a patient table in a bright clinic room">
    <defs>
      <linearGradient id="scanTone" x1="0" y1="0" x2="1" y2="1">
        <stop offset="0" stop-color="#eef1f5"/>
        <stop offset="0.6" stop-color="#dde3ea"/>
        <stop offset="1" stop-color="#b9d9f3"/>
      </linearGradient>
    </defs>
    <path d="M15 0 H445 V480 H95 Q15 380 15 200 Z" fill="url(#scanTone)"/>
    <path d="M15 0 Q15 260 70 362" fill="none" stroke="var(--bright-blue)" stroke-width="12"/>
  </svg>

  <article class="headline-card">
    <h1>Precision in Diagnostics,<br>Care from the Heart</h1>
    <p class="tagline">Leading in Cardiac Imaging</p>
  </article>

  <div class="footer-band"></div>
  <ul class="social-list" aria-label="Social channels">
    <li aria-label="Social channel"></li>
    <li class="divider" aria-hidden="true"></li>
    <li aria-label="Video channel"></li>
    <li class="divider" aria-hidden="true"></li>
    <li aria-label="Social channel"></li>
  </ul>

  <div class="logo-plate">
    <span class="logo-dot" aria-hidden="true"></span>
    <span class="logo-name">Vortal Med</span>
  </div>
</main>
</body>
</html>
```